Digital One Pager for Consulting Practice

I would like the essence of the content in my ppt consolidated into a one-pager. The one-pager will mainly be sent via email as a pdf and intended to excite and invite new clients and establish the credibility of my boutique high-end consulting firm. Infographics and symbols would be a plus. The target client should view the firm as providing premeir service. The client is getting a thought partner.

Target Market(s)

Large Medical Device Manufacturer Executives, Early-Stage Medical Device Manufacturer Executives, Partners at VC Firms

Industry/Entity Type

Medical Equipment

Colors
0355a3
f37122

Requirements
Must have
• Please match the color scheme in ppt. Please use the existing logo. I am very open to better graphics on the process. My photo does not need to be on the digital flyer. Hyper link to the website and email is needed.
Nice to have
• Infographics

```html
<!DOCTYPE html>
<html lang="en">
<head>
<meta charset="utf-8">
<title>Kestrel Advisory – One Pager</title>
<link href="https://fonts.googleapis.com/css2?family=Cinzel:wght@600;700&family=Roboto:wght@400;500;700&display=swap" rel="stylesheet">
<style>
  :root{
    --navy:#2b3956;
    --navy-deep:#1f2a42;
    --slate:#4a5877;
    --orange:#e8572a;
    --mist:#e4e8ef;
    --paper:#f3f5f8;
    --backdrop:#e6ddd7;
    --ink:#2c3448;
    --white:#ffffff;
  }
  *{box-sizing:border-box;margin:0;padding:0}
  html,body{width:1200px;height:790px;overflow:hidden;background:var(--backdrop);font-family:"Roboto",Arial,sans-serif;color:var(--ink)}
  a{color:inherit;text-decoration:none}
  .page{position:absolute;left:310px;top:20px;width:580px;height:750px;background:var(--paper);overflow:hidden;box-shadow:0 6px 18px rgba(60,40,30,.25)}
  .pattern-top{position:absolute;left:0;top:0;width:580px;height:215px;background:linear-gradient(160deg,var(--navy-deep) 0%,var(--slate) 55%,#8591aa 100%)}
  .pattern-mid{position:absolute;left:0;top:215px;width:580px;height:260px;background:linear-gradient(180deg,#b9c1d1 0%,#e6e9ef 45%,#cfd5e0 100%)}
  .pattern-foot{position:absolute;left:0;bottom:0;width:580px;height:110px;background:linear-gradient(180deg,#c9cfdb 0%,var(--slate) 60%,var(--navy-deep) 100%)}
  .brand{position:absolute;left:185px;top:18px;width:210px;height:44px;background:var(--white);border:2px solid var(--navy);border-radius:10px;display:flex;align-items:center;justify-content:center;gap:8px}
  .brand-dot{width:14px;height:14px;border-radius:50%;background:var(--orange)}
  .brand-name{font-family:"Cinzel",serif;font-weight:700;font-size:16px;color:var(--navy);letter-spacing:.5px;white-space:nowrap}
  .title{position:absolute;left:0;top:70px;width:580px;text-align:center;font-family:"Cinzel",serif;font-weight:700;font-size:16px;color:var(--white);letter-spacing:.4px;white-space:nowrap}
  .pill{position:absolute;background:var(--mist);color:var(--orange);font-family:"Cinzel",serif;font-weight:700;font-size:10px;padding:4px 12px;border-radius:10px;letter-spacing:.4px;white-space:nowrap}
  .pill-process{left:222px;top:96px}
  .pill-network{left:440px;top:60px}
  .pill-experience{left:30px;top:148px}
  .hub{position:absolute;left:190px;top:118px;width:200px;height:180px}
  .differentiators{position:absolute;left:0;top:296px;width:580px;text-align:center;font-family:"Cinzel",serif;font-weight:700;font-size:12px;color:var(--orange)}
  .panel{position:absolute;border:2.5px solid var(--navy);border-radius:14px;background:rgba(243,245,248,.78);padding:26px 10px 8px;overflow:hidden}
  .panel-tab{position:absolute;top:-2px;left:-2px;right:-2px;height:22px;background:var(--navy);border-radius:12px 12px 4px 4px;color:var(--white);font-family:"Cinzel",serif;font-weight:700;font-size:10px;padding:5px 10px;white-space:nowrap}
  .panel-experience{left:18px;top:240px;width:172px;height:222px}
  .panel-provide{left:200px;top:314px;width:180px;height:150px}
  .panel-services{left:392px;top:205px;width:172px;height:245px}
  .panel h4{font-size:9px;font-weight:700;color:var(--orange);margin:3px 0 2px;line-height:1.15}
  .panel ul{list-style:none}
  .panel li{position:relative;font-size:8.4px;line-height:1.25;padding-left:10px;margin-bottom:4px}
  .panel li::before{content:"";position:absolute;left:0;top:3px;width:5px;height:5px;background:var(--orange)}
  .panel-provide li{margin-bottom:2px}
  .panel-services li{margin-bottom:2px}
  .flow{position:absolute;left:18px;top:470px;width:546px;height:70px;border:2.5px solid var(--navy);border-radius:14px;background:rgba(243,245,248,.6)}
  .flow-svg{position:absolute;left:0;top:0}
  .band{position:absolute;left:18px;width:546px;height:42px;border:2.5px solid var(--navy);border-radius:12px;background:var(--mist);display:flex;align-items:center;padding-left:14px;gap:10px}
  .band-label{font-family:"Cinzel",serif;font-weight:700;font-size:11px;color:var(--navy);white-space:nowrap}
  .band-process{top:548px}
  .band-network{top:598px}
  .partners{display:flex;gap:14px;align-items:center;margin-left:30px}
  .partner{width:56px;height:20px;background:var(--slate);border-radius:3px;opacity:.75}
  .partner.round{width:22px;border-radius:50%}
  .contact{position:absolute;display:flex;align-items:center;gap:6px;font-size:10px;color:var(--white);font-weight:500;white-space:nowrap}
  .contact-phone{left:230px;top:656px}
  .contact-email{left:400px;top:656px}
  .contact-web{left:22px;top:716px}
</style>
</head>
<body>
<main class="page">
  <div class="pattern-top" role="img" aria-label="Faceted navy triangle pattern background"></div>
  <div class="pattern-mid" role="img" aria-label="Soft grey faceted triangle pattern"></div>
  <div class="pattern-foot" role="img" aria-label="Faceted navy triangle pattern footer"></div>

  <div class="brand"><span class="brand-dot"></span><span class="brand-name">KESTREL ADVISORY</span></div>
  <h1 class="title">KESTREL ADVISORY VALUE</h1>
  <span class="pill pill-process">EFFICIENT PROCESS</span>
  <span class="pill pill-network">VALUED NETWORK</span>
  <span class="pill pill-experience">EXTENSIVE EXPERIENCE</span>

  <svg class="hub" viewBox="0 0 200 180" aria-label="Experience, network and process combine into leverage">
    <circle cx="100" cy="88" r="70" fill="none" stroke="var(--orange)" stroke-width="3"/>
    <g fill="var(--navy-deep)" stroke="var(--white)" stroke-width="1.5">
      <circle cx="42" cy="42" r="28"/><circle cx="158" cy="36" r="28"/>
      <circle cx="100" cy="150" r="28"/><circle cx="100" cy="90" r="32"/>
    </g>
    <g fill="none" stroke="var(--white)" stroke-width="1.6">
      <path d="M34 54v-8a12 12 0 1 1 18 -4v12"/><circle cx="44" cy="34" r="3"/>
      <circle cx="158" cy="30" r="4"/><circle cx="146" cy="20" r="2.5"/><circle cx="170" cy="20" r="2.5"/><circle cx="146" cy="42" r="2.5"/><circle cx="170" cy="42" r="2.5"/>
      <path d="M148 22l7 5M168 22l-7 5M148 40l7-7M168 40l-7-7"/>
      <path d="M100 74v22M84 80h32M84 80l-6 12h12zM116 80l-6 12h12zM92 100h16"/>
      <circle cx="100" cy="146" r="7"/><circle cx="100" cy="146" r="12" stroke-dasharray="4 3"/>
    </g>
    <g font-family="Roboto,Arial,sans-serif" font-size="5" fill="var(--white)" text-anchor="middle">
      <text x="42" y="62">EXPERIENCE</text><text x="158" y="56">NETWORK</text>
      <text x="100" y="114" font-size="6" font-weight="700">LEVERAGE</text><text x="100" y="170">PROCESS</text>
    </g>
  </svg>

  <p class="differentiators">DIFFERENTIATORS</p>

  <section class="panel panel-experience">
    <div class="panel-tab">EXPERIENCE</div>
    <ul>
      <li>Over a decade @FDA (Former Deputy Division Director)</li>
      <li>Expertise: Cardiovascular, Ophthalmology, General Hospital, Infection Control, Dental, Anesthesia, Respiratory</li>
      <li>Vice President Regulatory Affairs / Quality Assurance @Halvorsen (Fortune 150 Company)</li>
      <li>Initiated reorganization of department</li>
      <li>Led major compliance effort</li>
      <li>Successful FDA inspection (no observations)</li>
    </ul>
  </section>

  <section class="panel panel-provide">
    <div class="panel-tab">EXPERIENCE TO PROVIDE</div>
    <h4>Executive Application Review</h4>
    <ul>
      <li>Examples include: Presubmission, IDE, 510(k), 513(g), PMA, Refuse to Accept, Hold letter</li>
      <li>Troubleshooting</li>
    </ul>
    <h4>Strategic Advice &amp; Diligence to Investors</h4>
    <ul>
      <li>Validate &amp; Verify Founder Milestones</li>
      <li>Diligence portfolio company Regulatory and Quality systems</li>
    </ul>
  </section>

  <section class="panel panel-services">
    <div class="panel-tab">SERVICES</div>
    <h4>Regulatory Strategy</h4>
    <ul><li>RAQA Organizational Structure</li><li>Regulatory Pathway</li></ul>
    <h4>FDA Communications</h4>
    <ul><li>Deficiency Response</li><li>Application Review</li></ul>
    <h4>Interim Executive Training Leadership</h4>
    <ul><li>Compliance Remediation</li><li>Accelerated Product Registration</li></ul>
    <h4>Training</h4>
    <ul><li>FDA Communication</li><li>MDR Reporting</li></ul>
  </section>

  <div class="flow">
    <svg class="flow-svg" width="541" height="65" viewBox="0 0 541 65" aria-label="Process steps: exploratory call, regulatory landscape, problem statement, review and align on deliverables">
      <g fill="var(--navy-deep)" stroke="var(--white)" stroke-width="1">
        <rect x="170" y="32" width="80" height="28" rx="7"/>
        <rect x="264" y="22" width="80" height="28" rx="7"/>
        <rect x="358" y="13" width="80" height="28" rx="7"/>
        <rect x="452" y="4" width="82" height="36" rx="7"/>
      </g>
      <g stroke="var(--orange)" stroke-width="5" stroke-linecap="round">
        <path d="M252 44l10-8M346 34l10-8M440 26l10-6"/>
      </g>
      <g font-family="Roboto,Arial,sans-serif" font-size="8.5" font-weight="500" fill="var(--white)" text-anchor="middle">
        <text x="210" y="44">Exploratory</text><text x="210" y="54">Call</text>
        <text x="304" y="34">Regulatory</text><text x="304" y="44">Landscape</text>
        <text x="398" y="25">Problem</text><text x="398" y="35">Statement</text>
        <text x="493" y="16">Review &amp;</text><text x="493" y="26">Align on</text><text x="493" y="36">Deliverables</text>
      </g>
    </svg>
  </div>

  <div class="band band-process">
    <span class="band-label">Efficient Process</span>
    <svg width="46" height="20" viewBox="0 0 46 20" aria-hidden="true"><path d="M0 6h30V0l16 10-16 10v-6H0z" fill="var(--navy)"/></svg>
  </div>
  <div class="band band-network">
    <span class="band-label">Valued Partner Network</span>
    <svg width="46" height="20" viewBox="0 0 46 20" aria-hidden="true"><path d="M0 6h30V0l16 10-16 10v-6H0z" fill="var(--navy)"/></svg>
    <div class="partners" aria-label="Partner organisations">
      <span class="partner"></span><span class="partner round"></span><span class="partner"></span><span class="partner"></span><span class="partner round"></span>
    </div>
  </div>

  <a class="contact contact-phone" href="tel:2025550148">
    <svg width="12" height="14" viewBox="0 0 12 14"><rect x="1" y="0.5" width="10" height="13" rx="2" fill="none" stroke="currentColor" stroke-width="1.3"/><circle cx="6" cy="11" r="1" fill="currentColor"/></svg>
    202.555.0148
  </a>
  <a class="contact contact-email" href="mailto:info@kestreladvisory.com">
    <svg width="16" height="12" viewBox="0 0 16 12"><rect x="0.7" y="0.7" width="14.6" height="10.6" fill="none" stroke="currentColor" stroke-width="1.3"/><path d="M1 1l7 6 7-6" fill="none" stroke="currentColor" stroke-width="1.3"/></svg>
    info@kestreladvisory.com
  </a>
  <a class="contact contact-web" href="https://www.kestreladvisory.com">
    <svg width="14" height="14" viewBox="0 0 14 14"><circle cx="7" cy="7" r="6" fill="none" stroke="currentColor" stroke-width="1.2"/><path d="M1 7h12M7 1c-3 3-3 9 0 12M7 1c3 3 3 9 0 12" fill="none" stroke="currentColor" stroke-width="1"/></svg>
    www.kestreladvisory.com
  </a>
</main>
</body>
</html>
```